Velmaro Partners Logo and Business Card Design

We already have the rough logo shape (however please make the lines on the logo much thicker so a dark background is not required to see it) . see photos uploaded.
It needs to be refined with color and digitized and then have a front and back business card layout done.
The services are high vibration healing support through a therapy and feng shui service offering. We want people to Feel Happiness, Feel Prosperity and Feel Peace. (the back of the card would have these phrases on it) So a warm, calm and peaceful feeling card.
We would like the card to use the logo provided (with thicker lines and color added) but below the graphic please use the name "Velmaro Partners" NOT Velmaro.
We also would like to use the colors in the colorized matrix shown in photos (gold and purple) but on the lighter side. Thanks for your time!

Front of Card should include: Logo, with Company Name: Velmaro Partners as part of logo, Name: Tomas Brekke email: tomas@velmaro.example web: www.velmaro.example mobile: 555.018.2264 at bottom of front list Family Constellation | Feng Shui

Back of Card should have the logo and the following listed vertically:

PERSONAL | BUSINESS (Larger size then smaller bullet items below)
*Find Happiness
*Find Prosperity
*Find Peace

Target Market(s)

Target market is both business and personal

Contact Information for Business Card

Front of Card should include: Logo, with Company Name: Velmaro Partners as part of logo, Name: Tomas Brekke email: tomas@velmaro.example web: www.velmaro.example mobile: 555.018.2264 at bottom of front list Family Constellation | Feng Shui ++++ Back of Card should have the logo and the following listed vertically: PERSONAL | BUSINESS (Larger size then smaller bullet items below) *Find Happiness *Find Prosperity *Find Peace

Font styles to use
Sans Serif

Colors

Designer to choose colors to be used in the design.

Requirements
Nice to have
• Nice light contrast color for the back of card background
Should not have
• No dark colored background on Card.

```html
<!DOCTYPE html>
<html lang="en">
<head>
<meta charset="utf-8">
<title>Velmaro Partners – Business Cards</title>
<link href="https://fonts.googleapis.com/css2?family=Montserrat:wght@400;500;600;700&display=swap" rel="stylesheet">
<style>
  :root{
    --stage:#e9e6e2;
    --card:#fbf8f2;
    --gold:#e2ad1f;
    --gold-text:#c9961a;
    --purple:#7b62b8;
    --ink:#2b2b2d;
    --muted:#55555a;
    --faint:#f0eadc;
  }
  *{margin:0;padding:0;box-sizing:border-box}
  html,body{width:1200px;height:786px;overflow:hidden;background:var(--stage);font-family:"Montserrat",sans-serif}
  .stage{position:relative;width:1200px;height:786px}
  .card{position:absolute;width:520px;height:300px;background:var(--card);border-radius:4px;overflow:hidden;box-shadow:0 10px 28px rgba(0,0,0,.18)}
  .card--front{left:50px;top:243px}
  .card--back{left:630px;top:243px}

  .faint-mark{position:absolute;left:-70px;top:40px;width:200px;height:200px;border-radius:50%;border:14px solid var(--faint)}

  .brand{display:flex;align-items:center;gap:10px;color:var(--gold-text);font-weight:600;letter-spacing:.06em;text-transform:uppercase}
  .brand__dot{border-radius:50%;border:3px solid var(--purple);flex:none}
  .card--front .brand{position:absolute;right:40px;top:56px;font-size:25px}
  .card--front .brand__dot{width:30px;height:30px}

  .rule{position:absolute;left:150px;right:40px;top:128px;height:1px;background:var(--gold)}

  .person{position:absolute;left:28px;top:150px;z-index:2}
  .person__name{color:var(--gold-text);font-weight:700;font-size:20px;letter-spacing:.04em;text-transform:uppercase}
  .person__role{color:var(--muted);font-size:12px;margin-top:1px}
  .person__rule{width:150px;height:1px;background:var(--gold);margin:7px 0 6px}
  .contact{list-style:none;color:var(--ink);font-size:11.5px;line-height:17px}
  .contact li{display:flex;align-items:center;gap:8px}
  .contact svg{width:10px;height:10px;flex:none}

  .bands{position:absolute;left:0;bottom:0;width:520px;height:90px}
  .services{position:absolute;right:26px;bottom:26px;color:var(--ink);font-size:12.5px;font-weight:500;z-index:2}

  .card--back .brand-block{position:absolute;left:0;right:0;top:78px;display:flex;flex-direction:column;align-items:center}
  .card--back .brand{font-size:30px}
  .card--back .brand__dot{width:36px;height:36px}
  .pill{margin-top:22px;background:var(--gold);color:var(--ink);font-weight:700;font-size:13px;letter-spacing:.03em;padding:4px 14px;border-radius:14px}
  .values{margin-top:14px;color:var(--ink);font-size:11.5px;display:flex;gap:8px;align-items:center}
  .values .bullet{width:4px;height:4px;border-radius:50%;background:var(--gold)}
</style>
</head>
<body>
<main class="stage">

  <section class="card card--front" aria-label="Business card front">
    <div class="faint-mark"></div>
    <div class="brand"><span class="brand__dot"></span>Velmaro Partners</div>
    <div class="rule"></div>

    <div class="person">
      <div class="person__name">Tomas Brekke</div>
      <div class="person__role">Owner</div>
      <div class="person__rule"></div>
      <ul class="contact">
        <li><svg viewBox="0 0 10 10"><path fill="#e2ad1f" d="M2 1h2l1 2-1.2 1a5 5 0 0 0 2.2 2.2L7 5l2 1v2a1 1 0 0 1-1 1A7 7 0 0 1 1 2a1 1 0 0 1 1-1z"/></svg>555.018.2264</li>
        <li><svg viewBox="0 0 10 10"><rect x="0.5" y="2" width="9" height="6" fill="#e2ad1f"/><path d="M.5 2l4.5 3.5L9.5 2" stroke="#fbf8f2" fill="none" stroke-width="1"/></svg>tomas@velmaro.example</li>
        <li><svg viewBox="0 0 10 10"><circle cx="5" cy="5" r="4.5" fill="#e2ad1f"/><path d="M.5 5h9M5 .5c-2 2.5-2 6.5 0 9M5 .5c2 2.5 2 6.5 0 9" stroke="#fbf8f2" fill="none" stroke-width=".7"/></svg>www.velmaro.example</li>
      </ul>
    </div>

    <svg class="bands" viewBox="0 0 520 90" aria-hidden="true">
      <path fill="#7b62b8" d="M0 66 L284 66 L280 76 L0 76 Z"/>
      <path fill="#e2ad1f" d="M0 76 L280 76 Q289 76 292 67 L302 40 Q306 30 318 30 L520 30 L520 90 L0 90 Z"/>
    </svg>
    <div class="services">Family Constellation | Feng Shui</div>
  </section>

  <section class="card card--back" aria-label="Business card back">
    <div class="brand-block">
      <div class="brand"><span class="brand__dot"></span>Velmaro Partners</div>
      <div class="pill">PERSONAL | BUSINESS</div>
      <div class="values">
        <span>Find Happiness</span><span class="bullet"></span>
        <span>Find Prosperity</span><span class="bullet"></span>
        <span>Find Peace</span>
      </div>
    </div>
  </section>

</main>
</body>
</html>
```